Brimlow Plumbing Solutions

This is for my new plumbing company, I have attached an example of what I’m going for but want it to look better.

Target Market(s)

Home owners, real estate, etc.

Industry/Entity Type

Plumbing

Font styles to use
Other font styles liked:
• As per my logo and other examples uploaded

Colors

Designer to choose colors to be used in the design.

Requirements
Must have
• Must include my logo provided and similar to my flyer I have attached but better

```html
<!DOCTYPE html>
<html lang="en">
<head>
<meta charset="UTF-8">
<title>Brimlow Plumbing Solutions – Flyer</title>
<link rel="stylesheet" href="https://fonts.googleapis.com/css2?family=Source+Sans+3:wght@400;500;600;700&display=swap">
<style>
  :root{
    --backdrop:#d8d8d8;
    --paper:#ffffff;
    --navy:#1b2340;
    --blue:#3a95d0;
    --sky:#6cb8e6;
    --orange:#f39c1f;
    --ink:#1e2433;
    --tile:#dbeaf5;
  }
  *{box-sizing:border-box;margin:0;padding:0}
  html,body{width:1200px;height:1200px;overflow:hidden}
  body{background:var(--backdrop);font-family:"Source Sans 3",Arial,sans-serif;color:var(--ink);position:relative}
  .flyer{position:absolute;left:238px;top:73px;width:724px;height:1054px;background:var(--paper);overflow:hidden}

  .brand{position:absolute;left:34px;top:40px;display:flex;align-items:center;gap:12px}
  .brand-dot{width:46px;height:46px;border-radius:50%;background:var(--blue)}
  .brand-name{font-weight:700;font-size:22px;line-height:1.05;color:var(--navy);width:190px}

  .callout-badge{position:absolute;left:492px;top:0;width:232px;height:78px;background:var(--blue);color:#fff;font-size:23px;font-weight:500;display:flex;align-items:center;justify-content:center}
  .callout-rule{position:absolute;left:492px;top:78px;width:232px;height:7px;background:var(--orange)}

  .stripe{position:absolute;left:0;top:136px;width:724px;height:47px}

  .hero{position:absolute;left:0;top:183px;width:724px;height:383px;background:var(--navy);overflow:hidden}
  .hero-headline{position:absolute;left:0;top:30px;width:100%;text-align:center;color:#fff;font-weight:500;font-size:25px;line-height:34px}
  .hero-art{position:absolute;left:436px;top:144px;width:304px;height:304px;border-radius:50%;background:radial-gradient(circle at 45% 40%,#7cc3ec,var(--sky) 70%)}
  .offer{position:absolute;left:62px;top:135px;width:228px;height:228px;border-radius:50%;background:var(--blue);border:6px solid #fff;color:#fff;text-align:center;display:flex;flex-direction:column;justify-content:center;align-items:center}
  .offer-lead{font-size:20px;line-height:25px;font-weight:500}
  .offer-amount{font-size:36px;font-weight:700;color:var(--orange);line-height:44px;margin-top:4px}
  .offer-tail{font-size:19px;font-weight:500}

  .services-title{position:absolute;left:0;top:590px;width:100%;text-align:center;font-size:37px;font-weight:700;color:var(--navy)}
  .services-rule{position:absolute;left:248px;top:638px;width:228px;height:3px;background:var(--blue)}
  .service-grid{position:absolute;left:30px;top:660px;width:664px;display:grid;grid-template-columns:repeat(4,1fr);row-gap:22px}
  .service{display:flex;flex-direction:column;align-items:center;text-align:center}
  .service-icon{width:54px;height:54px;border-radius:10px;background:var(--tile);border:2px solid var(--navy)}
  .service-name{margin-top:16px;font-size:17px;font-weight:500;line-height:19px;color:var(--ink);min-height:38px}

  .footer{position:absolute;left:0;top:946px;width:724px;height:108px;background:var(--blue);color:#fff;display:flex;align-items:center;padding:0 30px;gap:28px}
  .contact{display:flex;align-items:center;gap:8px}
  .contact-phone{font-size:19px;font-weight:600}
  .contact-email{font-size:14px}
  .contact-social{font-size:14px}
  .social-dot{width:20px;height:20px;border-radius:50%;border:2px solid #fff}
</style>
</head>
<body>
<main class="flyer">
  <div class="brand">
    <span class="brand-dot"></span>
    <span class="brand-name">Brimlow Plumbing Solutions</span>
  </div>
  <div class="callout-badge">Callout Badge</div>
  <div class="callout-rule"></div>

  <svg class="stripe" viewBox="0 0 724 47" width="724" height="47">
    <rect x="0" y="0" width="251" height="28" fill="#3a95d0"/>
    <polygon points="252,0 300,0 280,34 232,34" fill="#f39c1f"/>
    <rect x="284" y="22" width="440" height="6" fill="#3a95d0"/>
  </svg>

  <section class="hero">
    <p class="hero-headline">Your local reliable Sydney plumber —<br>specialists in Plumbing, Drainage &amp; Gas Maintenance</p>
    <div class="hero-art" role="img" aria-label="Illustration of a tap and pipework with valves"></div>
    <div class="offer">
      <span class="offer-lead">Mention this flyer<br>to receive</span>
      <span class="offer-amount">15% OFF</span>
      <span class="offer-tail">your first service!</span>
    </div>
  </section>

  <h2 class="services-title">Our Services</h2>
  <div class="services-rule"></div>
  <div class="service-grid">
    <div class="service"><div class="service-icon" role="img" aria-label="Emergency plumbing icon"></div><span class="service-name">Emergency Plumbing</span></div>
    <div class="service"><div class="service-icon" role="img" aria-label="Drainage icon"></div><span class="service-name">Drainage<br>Maintenance</span></div>
    <div class="service"><div class="service-icon" role="img" aria-label="Hot water icon"></div><span class="service-name">Hot Water Systems</span></div>
    <div class="service"><div class="service-icon" role="img" aria-label="Gas maintenance icon"></div><span class="service-name">Gas Maintenance</span></div>
    <div class="service"><div class="service-icon" role="img" aria-label="Leaking fixture icon"></div><span class="service-name">Leaking Fixtures</span></div>
    <div class="service"><div class="service-icon" role="img" aria-label="Blocked sewer icon"></div><span class="service-name">Blocked Sewer &amp;<br>Stormwater</span></div>
    <div class="service"><div class="service-icon" role="img" aria-label="Drain camera icon"></div><span class="service-name">Camera &amp; Locating</span></div>
    <div class="service"><div class="service-icon" role="img" aria-label="Valve maintenance icon"></div><span class="service-name">TMV Maintenance</span></div>
  </div>

  <footer class="footer">
    <div class="contact">
      <svg width="22" height="22" viewBox="0 0 24 24" fill="none" stroke="#fff" stroke-width="2" stroke-linejoin="round"><path d="M5 3h4l2 5-3 2a12 12 0 0 0 6 6l2-3 5 2v4a2 2 0 0 1-2 2A18 18 0 0 1 3 5a2 2 0 0 1 2-2z"/></svg>
      <span class="contact-phone">0400 555 218</span>
    </div>
    <div class="contact">
      <svg width="22" height="18" viewBox="0 0 24 18" fill="none" stroke="#fff" stroke-width="2"><rect x="1" y="1" width="22" height="16" rx="2"/><path d="M1 2l11 8 11-8"/></svg>
      <span class="contact-email">brimlowplumbing@mailbox.com</span>
    </div>
    <div class="contact">
      <span class="social-dot"></span>
      <span class="contact-social">@BrimlowPlumbing</span>
    </div>
  </footer>
</main>
</body>
</html>
```